Business Card Design

We need a business card designed for our new company. Prefer a black card with white logo & writing.

Contact Information for Business Card

Ted Galloway, address: 7-4812 Fernhollow Road, Abbotsford, BC, V3K 8R2, Office Phone: 604-712-3390, Cell: 604-947-2164, Email: ted@resinworkshub.ca

Colors

Designer to choose only greyscale colors for use in the design.

```html
<!DOCTYPE html>
<html lang="en">
<head>
<meta charset="utf-8">
<title>Resin Works Hub – Business Card</title>
<link href="https://fonts.googleapis.com/css2?family=Montserrat:wght@400;600;700&family=Poppins:wght@700&display=swap" rel="stylesheet">
<style>
  :root {
    --page-bg: #d6d6d6;
    --card-bg: #222222;
    --ink-light: #ffffff;
    --ink-soft: #e4e4e4;
    --ink-gloss: #111111;
    --card-shadow: rgba(0, 0, 0, 0.35);
  }
  * { margin: 0; padding: 0; box-sizing: border-box; }
  html, body {
    width: 900px; height: 1200px; overflow: hidden;
    background: var(--page-bg);
    font-family: "Montserrat", Arial, sans-serif;
  }
  .canvas { position: relative; width: 900px; height: 1200px; }
  .card {
    position: absolute;
    background: var(--card-bg);
    border-radius: 22px;
    box-shadow: 0 10px 24px var(--card-shadow);
  }
  .card--front { left: 80px; top: 131px; width: 742px; height: 441px; }
  .card--back  { left: 78px; top: 638px; width: 744px; height: 440px; }

  .brand {
    position: absolute; left: 0; right: 0;
    display: flex; align-items: center; justify-content: center; gap: 14px;
    font-family: "Poppins", Arial, sans-serif; font-weight: 700;
    letter-spacing: 1px; white-space: nowrap;
  }
  .brand__mark { width: 22px; height: 22px; border-radius: 50%; }
  .card--front .brand { top: 92px; font-size: 42px; color: var(--ink-light); }
  .card--front .brand__mark { background: var(--ink-light); }
  .card--back .brand { top: 180px; font-size: 52px; color: var(--ink-gloss); }
  .card--back .brand__mark { background: var(--ink-gloss); width: 26px; height: 26px; }

  .holder {
    position: absolute; right: 398px; top: 278px; text-align: right;
  }
  .holder__name { font-size: 24px; font-weight: 700; color: var(--ink-light); }
  .holder__role { margin-top: 8px; font-size: 15px; color: var(--ink-soft); }

  .divider {
    position: absolute; left: 371px; top: 257px;
    width: 2px; height: 100px; background: var(--ink-light);
  }
  .contacts {
    position: absolute; left: 393px; top: 253px; list-style: none;
  }
  .contacts li {
    display: flex; align-items: center; gap: 11px;
    height: 26px; margin-bottom: 1px;
    font-size: 15px; color: var(--ink-light);
  }
  .contacts svg { width: 16px; height: 16px; fill: var(--ink-light); flex: none; }

  .address {
    position: absolute; left: 0; right: 0; top: 388px;
    text-align: center; font-size: 16px; color: var(--ink-soft);
  }
</style>
</head>
<body>
<main class="canvas">
  <section class="card card--front" aria-label="Card front">
    <div class="brand"><span class="brand__mark"></span>RESIN WORKS HUB</div>

    <div class="holder">
      <div class="holder__name">Ted Galloway</div>
      <div class="holder__role">owner</div>
    </div>

    <div class="divider"></div>

    <ul class="contacts">
      <li>
        <svg viewBox="0 0 16 16" aria-hidden="true"><path d="M3.6 1.2l2.2 2.6-1.3 1.7c.9 2 2.3 3.4 4.2 4.4l1.7-1.3 2.6 2.2-1.3 2.4c-5.6-.6-9.9-5-10.5-10.6z"/></svg>
        604-712-3390
      </li>
      <li>
        <svg viewBox="0 0 16 16" aria-hidden="true"><path d="M4.5 0.5h7a1 1 0 0 1 1 1v13a1 1 0 0 1-1 1h-7a1 1 0 0 1-1-1v-13a1 1 0 0 1 1-1zm.6 2v9.5h5.8V2.5zM8 12.8a.9.9 0 1 0 0 1.8.9.9 0 0 0 0-1.8z"/></svg>
        604-947-2164
      </li>
      <li>
        <svg viewBox="0 0 16 16" aria-hidden="true"><path d="M1.5 3.5h13v1.2L8 8.8 1.5 4.7zM1.5 6.2L8 10.3l6.5-4.1v6.3h-13z"/></svg>
        ted@resinworkshub.ca
      </li>
      <li>
        <svg viewBox="0 0 16 16" aria-hidden="true"><path d="M8 1a7 7 0 1 0 0 14A7 7 0 0 0 8 1zm0 1.4c.8 0 1.7 1.8 2 4.3H6c.3-2.5 1.2-4.3 2-4.3zM2.5 8c0-.4 0-.9.2-1.3h2c-.1.9-.1 1.7 0 2.6h-2c-.2-.4-.2-.9-.2-1.3zm3.5 1.3c-.1-.9-.1-1.7 0-2.6h4c.1.9.1 1.7 0 2.6zm2 4.3c-.8 0-1.7-1.8-2-4.3h4c-.3 2.5-1.2 4.3-2 4.3zm3.3-4.3c.1-.9.1-1.7 0-2.6h2c.2.8.2 1.8 0 2.6z"/></svg>
        www.resinworkshub.ca
      </li>
    </ul>

    <p class="address">7-4812 Fernhollow Road, Abbotsford, BC, V3K 8R2</p>
  </section>

  <section class="card card--back" aria-label="Card back">
    <div class="brand"><span class="brand__mark"></span>RESIN WORKS HUB</div>
  </section>
</main>
</body>
</html>
```